Fin-Tech Firm Captivating Business Card Design

We need a logo design as well to compliment this business card.

We are a new startup based in Singapore called 'Brevora Technologies'.

We develop an array of financial solutions ranging from payment convenience to forex trading and remittance.

Our initial product is Pim - an application which allows user to pre-order food items which would be ready for pickup upon arrival.

We would like to see designs being in black and silver or whatever that looks appealing and exudes a fun and professional feel.

We're not picky as long as it doesn't look like common business cards will do.

I do have a current logo which i do not really like. It will be attached for reference sake

Info:

Brevora Technologies Pte. Ltd.
Company Registration no. 201678213K

FILE TO BE IN .AI and .PSD

Target Market(s)

-F&B (Online-Ordering)
-Finance(P2P Lending and Forex)

Industry/Entity Type

Finance

Contact Information for Business Card

Name
Position
Contact
Email
Address: 47 Merrow Street, Calder House, #14-03 Singapore 068215

Adrian Teo
Founder, Managing Director
+65 98471360
adrian.t@brevoratech.com

Kai Loh
Founder, Executive Director
+65 96603847
kai.l@brevoratech.com

Logo Text

Brevora Technologies

Font styles to use
Sans Serif

Requirements
Must have
• Something that has word play about link brev
• Minimalistic but also something that catches The Eye
• Gold/silver on white/black might be nice
• Animal logo ; horse, eagle, bull or bear
Nice to have
• Just make it look fun and cute
• Just a suggestion to make the Y of brevora stand out
Should not have
• Any landmarks of singapore
• Exclude Pte. Ltd.

```html
<!DOCTYPE html>
<html lang="en">
<head>
<meta charset="utf-8">
<title>Brevora Technologies – Business Card</title>
<link href="https://fonts.googleapis.com/css2?family=Source+Sans+3:wght@400;600;700&display=swap" rel="stylesheet">
<style>
  :root {
    --stage-top: #2a2a2a;
    --stage-bottom: #050505;
    --card-white: #f3f3f3;
    --brand-orange: #f2a616;
    --ink-dark: #1e1e1e;
    --ring-dark: #2b2b2b;
    --text-light: #ffffff;
  }
  * { margin: 0; padding: 0; box-sizing: border-box; }
  html, body { width: 1200px; height: 900px; overflow: hidden; }
  body {
    position: relative;
    background: linear-gradient(180deg, var(--stage-top) 0%, var(--stage-bottom) 100%);
    font-family: "Source Sans 3", "Myriad Pro", Arial, sans-serif;
  }
  .card {
    position: absolute;
    top: 184px;
    height: 490px;
    border-radius: 12px;
    box-shadow: 0 2px 6px rgba(0,0,0,0.45);
    overflow: hidden;
  }
  .card-front { left: 299px; width: 301px; background: var(--card-white); text-align: center; }
  .card-back { left: 645px; width: 304px; background: var(--brand-orange); }

  .brand-ring {
    position: absolute; left: 98px; top: 36px;
    width: 104px; height: 104px;
    border: 4px solid var(--ring-dark); border-radius: 50%;
  }
  .brand-name {
    position: absolute; left: 0; right: 0; top: 150px;
    color: var(--brand-orange); font-weight: 400; line-height: 1;
  }
  .brand-name .word { display: block; font-size: 50px; letter-spacing: 0.5px; }
  .brand-name .suffix { display: block; font-size: 21px; margin-top: 1px; }

  .person-name {
    position: absolute; left: 0; right: 0; top: 263px;
    color: var(--brand-orange); font-size: 19px; font-weight: 600;
  }
  .person-role {
    position: absolute; left: 0; right: 0; top: 286px;
    color: var(--ink-dark); font-size: 14px;
  }
  .address {
    position: absolute; left: 0; right: 0; top: 329px;
    color: var(--ink-dark); font-size: 14px; line-height: 21px; font-style: normal;
  }
  .contact {
    position: absolute; left: 0; right: 0; top: 395px;
    color: var(--ink-dark); font-size: 14px; line-height: 20px; list-style: none;
  }
  .contact svg { width: 10px; height: 10px; vertical-align: -1px; margin-right: 3px; fill: var(--brand-orange); }
  .registration {
    position: absolute; left: 0; right: 0; top: 446px;
    color: var(--ink-dark); font-size: 14px; font-weight: 700;
  }

  .back-name {
    position: absolute; left: 22px; top: 372px;
    color: var(--text-light); font-weight: 400; line-height: 1;
  }
  .back-name .word { display: block; font-size: 62px; letter-spacing: 0.5px; }
  .back-name .suffix { display: block; font-size: 25px; margin-top: 0; }
</style>
</head>
<body>
  <section class="card card-front" aria-label="Business card front">
    <div class="brand-ring" aria-hidden="true"></div>
    <h1 class="brand-name"><span class="word">BREVORA</span><span class="suffix">Technologies Pte. Ltd</span></h1>
    <p class="person-name">Adrian Teo</p>
    <p class="person-role">Founder, Managing Director</p>
    <address class="address">47 Merrow Street, Calder House,<br>#14-03 Singapore 068215</address>
    <ul class="contact">
      <li><svg viewBox="0 0 10 10" aria-hidden="true"><path d="M2.2 0.5 3.8 2.6 2.9 3.7C3.6 5.1 4.9 6.4 6.3 7.1L7.4 6.2 9.5 7.8 8.6 9.5C4.3 9.2 0.8 5.7 0.5 1.4Z"/></svg>+65 98471360</li>
      <li><svg viewBox="0 0 10 10" aria-hidden="true"><path d="M0.5 2h9v6h-9z M0.9 2.3 5 5.4 9.1 2.3" stroke="#f3f3f3" stroke-width="0.8"/></svg>adrian.t@brevoratech.com</li>
    </ul>
    <p class="registration">Company Registration no. 201678213K</p>
  </section>

  <section class="card card-back" aria-label="Business card back">
    <h2 class="back-name"><span class="word">BREVORA</span><span class="suffix">Technologies Pte. Ltd</span></h2>
  </section>
</body>
</html>
```